Small corporate website template design

I need a couple templates designed for a small corporate website. The corporate site reflects the existence of the parent company which will own various brands/services that have their own websites, so it will mainly be used to present who we are, what we do, what is happening (news/events), how to contact us, link off to our other brand/service sites, as well as post information for public relations, investors, and job opportunities.

The company name is Brelvanto LLC (www.brelvanto-example.com), and the name is representative of stratified layers of interconnected digital services. The corporate site is not expected to generate a bunch of fanfare - that honor will be reserved for the externally linked brand/service sites.

The provided logo may be manipulated in color, size, shape, positioning, etc. to get it to fit with the design, but should be integrated in some way.

What we are looking for is a home page layout as well as a template for an inner page whereby the navigation/logo, etc may be diminished to some extent for the inner pages. We are also interested in reusable elements such as dividers, content containers, etc. in order to represent the types of information described above that we would like to present as described above.

We are particularly interested in consistency of design elements, conservative use of color (including consideration of accessibility concerns), judicious use of whitespace in favor of simplified messaging, and something lending itself well to internationalization/translation.

Target Market(s)

Small business owners, entrepreneurs (B2B)

Number of Pages Required

2 page

Font styles to use
Sans Serif

Requirements
Must have
• See the attached PDF with the logo concept, color swatches, and comparative sites.

```html
<!DOCTYPE html>
<html lang="en">
<head>
<meta charset="utf-8">
<title>Brelvanto LLC</title>
<link rel="stylesheet" href="https://fonts.googleapis.com/css2?family=Raleway:wght@400;500;600;700&family=Open+Sans:wght@400;600&display=swap">
<style>
:root{
  --navy:#0d3b6f;
  --navy-deep:#082b55;
  --orange:#d5690f;
  --orange-soft:#e08a3c;
  --ink:#2c3440;
  --muted:#6d7480;
  --line:#d9dce1;
  --field:#eceef1;
  --white:#ffffff;
}
*{margin:0;padding:0;box-sizing:border-box}
html,body{width:1200px;height:4027px;overflow:hidden}
body{font-family:"Open Sans",Arial,sans-serif;color:var(--ink);background:var(--white);position:relative}
.abs{position:absolute}
h1,h2,h3,.nav,.btn,.tab{font-family:"Raleway",Arial,sans-serif}
.btn{position:absolute;border:2px solid var(--orange);color:var(--orange);font-weight:700;font-size:17px;letter-spacing:1px;text-align:center;background:transparent;text-transform:uppercase}
.section-title{position:absolute;left:0;width:1200px;text-align:center;font-family:"Raleway",Arial,sans-serif;font-weight:600;font-size:42px;color:var(--navy);letter-spacing:.5px}
.section-sub{position:absolute;left:0;width:1200px;text-align:center;color:var(--orange);font-size:18px;font-family:"Raleway",Arial,sans-serif;font-weight:500}
.wordmark{font-family:"Raleway",Arial,sans-serif;font-weight:700;color:var(--navy)}

/* hero */
.hero{position:absolute;left:0;top:0;width:1200px;height:650px;background:linear-gradient(180deg,#f6f7f9 0%,#eef0f3 100%);overflow:hidden}
.brand{left:80px;top:30px;font-size:30px;display:flex;align-items:center;gap:10px}
.brand .dot{width:16px;height:16px;background:var(--navy);border-radius:50%}
.nav{left:540px;top:40px;display:flex;gap:34px;font-size:17px;font-weight:500;color:var(--ink)}
.nav .active{color:var(--orange)}
.login{left:1008px;top:28px;width:116px;height:42px;line-height:38px;font-size:17px;font-weight:500;letter-spacing:.5px}
.hero-title{left:80px;top:190px;font-size:36px;line-height:52px;font-weight:700;color:var(--navy)}
.hero-title span{color:var(--orange)}
.hero-sub{left:80px;top:302px;font-size:17px;color:var(--ink)}
.get-started{left:78px;top:344px;width:170px;height:52px;line-height:48px;font-size:16px}
.hex-field{left:780px;top:118px;width:300px;height:520px;background:linear-gradient(160deg,#d7dfe9 0%,#e3d7cb 55%,#eef0f3 100%)}
.screen{left:242px;top:430px;width:676px;height:240px;background:linear-gradient(180deg,#1b1d22 0%,#2a2d33 100%);border-radius:14px 14px 0 0;padding:12px 14px 0}
.screen-inner{width:100%;height:100%;background:linear-gradient(180deg,#f4f5f7,#e8eaee)}
.slant{left:0;top:0}

/* services */
.services-grid{left:0;top:820px;width:1200px;height:270px}
.hex{position:absolute;width:228px;height:264px;clip-path:polygon(50% 0,100% 25%,100% 75%,50% 100%,0 75%,0 25%);background:var(--orange);color:var(--white);text-align:center}
.hex svg{position:absolute;left:74px;top:58px}
.hex p{position:absolute;left:0;width:228px;top:160px;font-size:18px;line-height:24px;font-family:"Raleway",Arial,sans-serif;font-weight:500;text-transform:uppercase}

/* welcome */
.welcome{left:0;top:1181px;width:1200px;height:417px;background:radial-gradient(ellipse at 70% 40%,#14508f 0%,var(--navy) 45%,var(--navy-deep) 100%)}
.welcome-photo{left:89px;top:81px;width:333px;height:282px;border-radius:0 40px 0 40px;background:linear-gradient(135deg,#c9ccd2 0%,#8b8e96 50%,#4c4f57 100%)}
.welcome h2{left:468px;top:72px;font-size:42px;font-weight:600;color:var(--white)}
.welcome .who{left:476px;top:130px;font-size:18px;color:var(--orange);font-family:"Raleway",Arial,sans-serif;font-weight:600}
.welcome .copy{left:476px;top:166px;width:560px;font-size:14.5px;line-height:28px;color:#d9e2ee}
.learn{left:474px;top:295px;width:166px;height:52px;line-height:48px;font-size:17px}

/* why */
.why{left:0;top:1598px;width:1200px;height:665px;background:linear-gradient(180deg,#fff 0%,#f3f4f6 100%)}
.tab{position:absolute;top:180px;font-size:16px;font-weight:700;color:var(--navy);letter-spacing:.3px}
.tab.active{color:var(--orange)}
.why .mark{left:0;width:1200px;top:286px;text-align:center;font-size:34px}
.why .copy{left:260px;width:680px;top:350px;text-align:center;font-size:15px;line-height:30px;color:var(--ink)}
.field{position:absolute;left:322px;width:551px;height:54px;background:var(--field);display:flex;align-items:center}
.field .icon{width:54px;height:54px;background:var(--orange);display:flex;align-items:center;justify-content:center}
.field span{margin-left:24px;font-size:14px;color:var(--muted)}
.submit{left:523px;width:156px;height:50px;line-height:46px;font-size:17px}

/* testimonials */
.clients{left:0;top:2263px;width:1200px;height:417px;background:linear-gradient(180deg,#d9781f 0%,var(--orange) 60%,#c95f0a 100%)}
.clients h2{left:0;width:1200px;top:52px;text-align:center;font-size:42px;font-weight:600;color:var(--navy)}
.client-photo{position:absolute;width:142px;height:164px;clip-path:polygon(50% 0,100% 25%,100% 75%,50% 100%,0 75%,0 25%);background:#fff}
.client-photo div{position:absolute;left:6px;top:7px;width:130px;height:150px;clip-path:polygon(50% 0,100% 25%,100% 75%,50% 100%,0 75%,0 25%);background:linear-gradient(160deg,#e6e2dc,#b7aea3)}
.quote{position:absolute;width:340px;font-size:14px;line-height:27px;color:#fbe9d8}
.client-name{position:absolute;font-size:14px;font-weight:600;color:var(--white);font-family:"Raleway",Arial,sans-serif;display:flex;align-items:center;gap:14px}
.client-name i{display:block;width:30px;height:3px;background:var(--white)}
.dots{left:552px;top:2628px;display:flex;gap:6px}
.dots i{display:block;width:28px;height:4px;background:rgba(255,255,255,.55)}
.dots i.on{background:var(--navy)}

/* news */
.news-card{position:absolute;top:2819px;width:334px}
.news-photo{width:334px;height:207px;position:relative;background:linear-gradient(135deg,#c7d1dd,#6e7f93)}
.news-photo.b{background:linear-gradient(135deg,#d6d3cf,#5e6570)}
.news-photo.c{background:linear-gradient(135deg,#17325a,#0a1830)}
.date{position:absolute;left:0;top:0;width:74px;height:82px;background:var(--orange);color:var(--white);text-align:center;font-family:"Raleway",Arial,sans-serif}
.date b{display:block;font-size:36px;line-height:40px;padding-top:8px;font-weight:600}
.date small{font-size:14px;text-transform:uppercase}
.news-card h3{margin-top:20px;font-size:20px;line-height:30px;color:var(--navy);font-weight:700}
.news-card p{margin-top:10px;font-size:13.5px;line-height:29px;color:var(--ink)}

/* contact */
.footer-band{left:0;top:0}
.contact-card{left:325px;top:3254px;width:550px;height:527px;background:var(--white);box-shadow:0 4px 22px rgba(0,0,0,.14)}
.contact-card h2{position:absolute;left:0;width:550px;top:36px;text-align:center;font-size:42px;font-weight:600;color:var(--navy)}
.contact-card .lead{position:absolute;left:0;width:550px;top:104px;text-align:center;color:var(--orange);font-size:15px;font-weight:600;font-family:"Raleway",Arial,sans-serif}
.line-field{position:absolute;left:37px;width:476px;height:44px;border-bottom:1px solid var(--line);display:flex;justify-content:space-between;align-items:center;font-size:13px;color:var(--muted)}
.footer-mark{left:0;width:1200px;top:3828px;text-align:center;font-size:34px;color:var(--white)}
.social{left:522px;top:3898px;display:flex;gap:16px}
.social i{display:block;width:44px;height:44px;border-radius:50%;background:var(--orange)}
.copyright{left:0;width:1200px;top:3956px;text-align:center;font-size:14px;color:#cdd6e2}
.copyright b{color:var(--orange);font-weight:600}
</style>
</head>
<body>

<header class="hero">
  <div class="abs hex-field" role="img" aria-label="Cluster of orange and navy hexagons of varying sizes"></div>
  <div class="abs screen"><div class="screen-inner" role="img" aria-label="Laptop screen previewing the home page"></div></div>
  <svg class="abs slant" width="1200" height="650" viewBox="0 0 1200 650" aria-hidden="true">
    <polygon points="0,572 1200,522 1200,650 0,650" fill="#ffffff"/>
    <line x1="0" y1="572" x2="1200" y2="522" stroke="#c9ccd2" stroke-width="2"/>
  </svg>
  <div class="abs brand wordmark"><span class="dot"></span>Brelvanto</div>
  <nav class="abs nav"><span class="active">HOME</span><span>ABOUT</span><span>SERVICES</span><span>NEWS</span><span>CONTACT</span></nav>
  <div class="btn login">LOGIN</div>
  <h1 class="abs hero-title">ADAPTIVE SOFTWARE TECHNOLOGY<br>FOR THE <span>DIGITAL REVOLUTION</span></h1>
  <p class="abs hero-sub">Digital Layers To Raise The Quality Of Life</p>
  <div class="btn get-started">GET STARTED</div>
</header>

<section>
  <h2 class="section-title" style="top:700px">OUR SERVICES</h2>
  <p class="section-sub" style="top:756px">What We Do</p>
  <div class="abs services-grid">
    <div class="hex" style="left:208px;top:0">
      <svg width="80" height="80" viewBox="0 0 80 80" fill="none" stroke="#fff" stroke-width="3"><rect x="8" y="6" width="64" height="44"/><circle cx="40" cy="28" r="13"/><line x1="40" y1="50" x2="26" y2="74"/><line x1="40" y1="50" x2="54" y2="74"/></svg>
      <p>MARKETING<br>STRATEGY</p>
    </div>
    <div class="hex" style="left:476px;top:0">
      <svg width="80" height="80" viewBox="0 0 80 80" fill="none" stroke="#fff" stroke-width="3"><rect x="14" y="40" width="10" height="30"/><rect x="34" y="14" width="10" height="56"/><rect x="54" y="30" width="10" height="40"/><line x1="6" y1="72" x2="74" y2="72"/></svg>
      <p>DIGITAL<br>ANALYTICS</p>
    </div>
    <div class="hex" style="left:759px;top:0">
      <svg width="80" height="80" viewBox="0 0 80 80" fill="none" stroke="#fff" stroke-width="3"><rect x="6" y="8" width="68" height="52"/><line x1="6" y1="18" x2="74" y2="18"/><circle cx="40" cy="40" r="10"/><line x1="28" y1="72" x2="52" y2="72"/></svg>
      <p>MANAGEMENT AND<br>OPTIMIZATION</p>
    </div>
  </div>
</section>

<section class="abs welcome">
  <div class="abs welcome-photo" role="img" aria-label="Team meeting around a laptop in an office"></div>
  <h2 class="abs">WELCOME TO BRELVANTO</h2>
  <p class="abs who">Who We Are</p>
  <p class="abs copy">Lorem Ipsum is simply dummy text of the printing and typesetting industry. Lorem Ipsum has been the industry's standard dummy text ever since the 1500s, when an unknown printer took a galley of type and scrambled it to make a type specimen book. It has survived not only five centuries.</p>
  <div class="btn learn">LEARN MORE</div>
</section>

<section class="abs why">
  <h2 class="section-title" style="top:48px">WHY BRELVANTO ?</h2>
  <p class="section-sub" style="top:104px;font-size:17px">What We offer</p>
  <svg class="abs" width="744" height="20" viewBox="0 0 744 20" aria-hidden="true" style="top:218px;left:226px">
    <line x1="8" y1="10" x2="736" y2="10" stroke="#d5690f" stroke-width="2"/>
    <circle cx="8" cy="10" r="7" fill="#d5690f"/><circle cx="736" cy="10" r="7" fill="#d5690f"/>
  </svg>
  <svg class="abs" width="250" height="60" viewBox="0 0 250 60" aria-hidden="true" style="left:642px;top:170px">
    <polyline points="0,58 22,2 228,2 250,58" fill="none" stroke="#d5690f" stroke-width="2"/>
  </svg>
  <span class="tab" style="left:292px">PUBLIC RELATIONS</span>
  <span class="tab" style="left:502px">INVESTORS</span>
  <span class="tab active" style="left:686px">JOB OPPORTUNITIES</span>
  <div class="abs mark wordmark">Brelvanto</div>
  <p class="abs copy">Lorem Ipsum is simply dummy text of the printing and typesetting industry. Lorem Ipsum has been the industry's standard dummy text ever since the.</p>
  <div class="field" style="top:424px"><div class="icon"><svg width="20" height="22" viewBox="0 0 20 22" fill="#fff"><circle cx="10" cy="6" r="5"/><path d="M0 22c0-7 4-10 10-10s10 3 10 10z"/></svg></div><span>Enter Email *</span></div>
  <div class="field" style="top:486px"><div class="icon"><svg width="22" height="16" viewBox="0 0 22 16" fill="#fff"><rect width="22" height="16"/><polyline points="1,1 11,9 21,1" fill="none" stroke="#d5690f" stroke-width="2"/></svg></div><span>Enter Email *</span></div>
  <div class="btn submit" style="top:554px">SUBMIT</div>
</section>

<section class="abs clients">
  <h2 class="abs">WHAT OUR CLIENT SAY</h2>
  <div class="client-photo" style="left:80px;top:167px"><div role="img" aria-label="Portrait of a client"></div></div>
  <p class="quote" style="left:250px;top:172px">" Lorem Ipsum is simply dummy text of the printing and typesetting industry. Lorem Ipsum has been the industry's standard dummy text ever since the lorem dummy text."</p>
  <div class="client-name" style="left:252px;top:284px"><i></i>CLIENT NAME</div>
  <div class="client-photo" style="left:623px;top:167px"><div role="img" aria-label="Portrait of a client"></div></div>
  <p class="quote" style="left:792px;top:172px">" Lorem Ipsum is simply dummy text of the printing and typesetting industry. Lorem Ipsum has been the industry's standard dummy text ever since the lorem dummy text."</p>
  <div class="client-name" style="left:794px;top:284px"><i></i>CLIENT NAME</div>
</section>
<div class="abs dots"><i></i><i class="on"></i><i></i></div>

<section>
  <h2 class="section-title" style="top:2734px">LATEST NEWS/EVENTS</h2>
  <article class="news-card" style="left:80px">
    <div class="news-photo" role="img" aria-label="Hands working on a laptop with charts"><div class="date"><b>19</b><small>May</small></div></div>
    <h3>Lorem Ipsum is simply dummy text of the printing types.</h3>
    <p>Lorem Ipsum is simply dummy text of the printing and typesetting industry. Lorem Ipsum has been the industry of type industry.</p>
  </article>
  <article class="news-card" style="left:432px">
    <div class="news-photo b" role="img" aria-label="Two businessmen reviewing documents"><div class="date"><b>19</b><small>May</small></div></div>
    <h3>Lorem Ipsum is simply dummy text of the printing types.</h3>
    <p>Lorem Ipsum is simply dummy text of the printing and typesetting industry. Lorem Ipsum has been the industry of type industry.</p>
  </article>
  <article class="news-card" style="left:787px">
    <div class="news-photo c" role="img" aria-label="Hand touching a glowing digital network interface"><div class="date"><b>19</b><small>May</small></div></div>
    <h3>Lorem Ipsum is simply dummy text of the printing types.</h3>
    <p>Lorem Ipsum is simply dummy text of the printing and typesetting industry. Lorem Ipsum has been the industry of type industry.</p>
  </article>
</section>

<footer>
  <svg class="abs footer-band" width="1200" height="4027" viewBox="0 0 1200 4027" aria-hidden="true">
    <defs><radialGradient id="bandGlow" cx="50%" cy="40%" r="70%"><stop offset="0" stop-color="#14508f"/><stop offset="1" stop-color="#082b55"/></radialGradient></defs>
    <polygon points="0,3760 1200,3570 1200,4027 0,4027" fill="url(#bandGlow)"/>
  </svg>
  <div class="abs contact-card">
    <h2>CONTACT US</h2>
    <p class="lead">Need a Free Quote, or Have a Question? Get In Touch!</p>
    <div class="line-field" style="top:142px"><span>Name *</span><svg width="14" height="15" viewBox="0 0 14 15" fill="#b9bec6"><circle cx="7" cy="4" r="4"/><path d="M0 15c0-5 3-7 7-7s7 2 7 7z"/></svg></div>
    <div class="line-field" style="top:208px"><span>Company *</span><svg width="12" height="8" viewBox="0 0 12 8" fill="#b9bec6"><polygon points="0,0 12,0 6,8"/></svg></div>
    <div class="line-field" style="top:272px"><span>Email *</span><svg width="15" height="11" viewBox="0 0 15 11" fill="#b9bec6"><rect width="15" height="11"/><polyline points="1,1 7.5,6 14,1" fill="none" stroke="#fff" stroke-width="1.5"/></svg></div>
    <div class="line-field" style="top:345px"><span>Phone *</span><svg width="14" height="14" viewBox="0 0 24 24" fill="#b9bec6"><path d="M6.6 10.8a15 15 0 0 0 6.6 6.6l2.2-2.2c.3-.3.7-.4 1-.2 1.1.4 2.3.6 3.6.6.6 0 1 .4 1 1V20c0 .6-.4 1-1 1A17 17 0 0 1 3 4c0-.6.4-1 1-1h3.5c.6 0 1 .4 1 1 0 1.3.2 2.5.6 3.6.1.3 0 .7-.2 1z"/></svg></div>
    <div class="btn submit" style="left:197px;top:432px">SUBMIT</div>
  </div>
  <div class="abs footer-mark wordmark" style="color:#fff">Brelvanto</div>
  <div class="abs social" aria-label="Social links"><i></i><i></i><i></i></div>
  <p class="abs copyright"><b>BRELVANTO</b> - 2018 All Right Reserved.</p>
</footer>

</body>
</html>
```